Wordpress website design for children’s entertainment agency

What is the aim of the website?

The aim for the website is to attract potential bookers and to get them to respond to the Call to action: contact the entertainer - phone call/request a call back/completing a form.
All the information needs to be easy to access and navigate to, especially on mobile view.
The call to action needs to be clear and easy to navigate.

What I need:

Critical - This website needs to look good on all devices.
Easy navigation on a mobile device is essential so the elements need to be bold and easy to click on with a thumb (when in mobile view)

The ‘grid area’ needs to be graphics based with simple descriptions, i.e. ‘magic shows’, Circus Clowns, Face painting, Costume Characters, Party Host, Carnival Parties, Balloon Sculpting, DJ and MC, Princess Parties, Holiday Parties, Fun Add Ons and Contact.

See: http://www.jollymarvin.com/
and http://playtimebookingnest.com/

I would like to see a sample page layout as well to see how your design would be carried through the site layout in the inside pages.

Target Market(s)

The site visitors are mainly mums, aged between 25 - 41. Other visitors will included event organisers looking for entertainment services for baptism, communions and sweet 16’s

Industry/Entity Type

Entertainment Industry

Number of Pages Required

1 page

Font styles to use
Sans Serif

Colors
6c459b
fbed22
0493ce

Requirements
Must have
• Critical - This website needs to look good on all devices.
• Easy navigation on a mobile device is essential so the elements need to be bold and easy to click on with a thumb (when in mobile view)
• The ‘grid area’ needs to be graphics based with simple descriptions, i.e. ‘magic shows’, Circus Clowns, Face painting, Costume Characters, Party Host, Carnival Parties, Balloon Sculpting, DJ and MC, Princess Parties, Holiday Parties, Fun Add Ons and Contact.
• See: http://www.jollymarvin.com/
• and http://playtimebookingnest.com/
Nice to have
• clean looking and fun with an element of ‘Trobel’ and stars (this is the exciting site http://gordysjoyshack.com/index.html)

```html
<!DOCTYPE html>
<html lang="en">
<head>
<meta charset="utf-8">
<title>Pippa's Party Barn – Children's Entertainment</title>
<link href="https://fonts.googleapis.com/css2?family=Lobster&family=Open+Sans:wght@400;600;700&display=swap" rel="stylesheet">
<style>
:root{
  --purple:#6c459b;
  --purple-dark:#4f2d7f;
  --purple-deep:#5a3590;
  --yellow:#fbed22;
  --gold:#f6c431;
  --blue:#0493ce;
  --blue-dark:#0b78b0;
  --ink:#333;
  --muted:#8a8a8a;
  --line:#e4e4e4;
  --white:#fff;
  --night:#050505;
}
*{box-sizing:border-box;margin:0;padding:0}
html,body{width:800px;height:1200px;overflow:hidden}
body{position:relative;background:var(--night);font-family:"Open Sans",sans-serif;color:var(--ink)}
.star-field{position:absolute;top:0;width:58px;height:1200px;
  background:radial-gradient(circle at 30% 20%,#3a1f55 0,transparent 40%),radial-gradient(circle at 60% 60%,#1f4a1a 0,transparent 40%),radial-gradient(circle at 40% 90%,#4a2060 0,transparent 40%),var(--night)}
.star-field.left{left:0}
.star-field.right{left:743px;width:57px}
.page{position:absolute;left:58px;top:0;width:685px;height:1200px;background:var(--white)}
.header{position:absolute;left:0;top:0;width:685px;height:104px;background:linear-gradient(#e9f4fb,#fff)}
.brand{position:absolute;left:16px;top:34px;display:flex;align-items:center;gap:8px;font-weight:700;font-size:19px;color:var(--purple)}
.brand .dot{width:22px;height:22px;border-radius:50%;background:var(--yellow)}
.btn-blue{background:linear-gradient(#18a6e0,var(--blue-dark));color:var(--white);border:1px solid #0a6a9c;border-radius:3px;display:flex;align-items:center;justify-content:center;font-weight:600}
.header .contact-btn{position:absolute;left:577px;top:22px;width:91px;height:28px;font-size:10.5px}
.phone{position:absolute;right:17px;top:67px;display:flex;align-items:center;gap:5px;font-size:14.5px;color:#444}
.nav{position:absolute;left:16px;top:104px;width:652px;height:42px;border-radius:3px;background:linear-gradient(#7b51ad,var(--purple-deep));border:1px solid #9b7cc4;display:flex;align-items:center;padding-left:24px}
.nav a{color:var(--white);text-decoration:none;font-size:7.8px;font-weight:600}
.nav .home{background:linear-gradient(#fde15a,var(--gold));color:var(--purple-dark);width:53px;height:26px;display:flex;align-items:center;justify-content:center;border-radius:2px}
.slider{position:absolute;left:16px;top:158px;width:484px;height:215px;background:#000;border:1px solid #444}
.slider .art{position:absolute;left:28px;top:8px;width:155px;height:206px;background:linear-gradient(135deg,#c4231f,#e8c53a 45%,#2b49c8)}
.slider h1{position:absolute;left:201px;top:92px;font-family:"Lobster",cursive;font-weight:400;font-size:16px;line-height:27px;color:var(--white)}
.dots{position:absolute;left:428px;top:192px;display:flex;gap:4px}
.dots i{width:7px;height:7px;border-radius:50%;background:#7b51ad}
.dots i.on{background:var(--yellow)}
.quick-form{position:absolute;left:518px;top:158px;width:150px;height:204px;border:1px solid #9ad;border-radius:2px;background:linear-gradient(160deg,#2fa9d6,#59c3e4 45%,#0f6fa8 75%,#5bd0a4)}
.quick-form h2{font-family:"Lobster",cursive;font-weight:400;color:var(--white);font-size:16px;text-align:center;margin-top:10px}
.field{position:absolute;background:var(--white);border:1px solid #cfd8de;border-radius:2px;font-size:7px;color:#999;padding-left:8px;display:flex;align-items:center}
.quick-form .field{left:10px;width:128px;height:25px}
.quick-form .submit{position:absolute;left:66px;top:163px;width:71px;height:27px;font-size:8px}
.section-title{font-family:"Lobster",cursive;font-weight:400;color:var(--purple)}
.news-title{position:absolute;left:518px;top:376px;font-size:14px;color:#333}
.news-item{position:absolute;left:518px;width:150px;height:46px}
.news-item .thumb{position:absolute;left:0;top:0;width:55px;height:46px;border:2px solid #d8d8d8}
.news-item p{position:absolute;left:66px;top:2px;width:86px;font-size:7.4px;line-height:13.6px;color:#444}
.offers{position:absolute;left:518px;top:586px;width:150px;height:100px;border:1px solid #2a5a8a;background:linear-gradient(#6c8fb0,#d9c88f 65%,#343434)}
.offers span{position:absolute;left:0;right:0;bottom:4px;text-align:center;font-family:"Lobster",cursive;color:var(--white);font-size:17px}
.grid{position:absolute;left:16px;top:388px;width:484px;display:grid;grid-template-columns:repeat(4,116px);grid-auto-rows:93px;column-gap:6px;row-gap:10px}
.tile{position:relative;border:1px solid #cfc3df;border-radius:3px;overflow:hidden}
.tile .photo{position:absolute;inset:0}
.tile .label{position:absolute;left:0;right:0;bottom:0;height:26px;background:linear-gradient(#8a63bb,var(--purple-deep));border-top-left-radius:8px;border-top-right-radius:8px;color:var(--white);font-family:"Lobster",cursive;font-size:9px;display:flex;align-items:center;justify-content:center}
.divider{position:absolute;left:0;top:714px;width:685px;height:1px;background:var(--line)}
.welcome{position:absolute;left:16px;top:726px;width:652px}
.welcome h2{font-size:18px;line-height:22px;margin-bottom:4px}
.welcome p{font-size:7px;line-height:20.6px;color:var(--muted)}
.welcome .cta{margin-top:5px;width:182px;height:31px;font-size:10px;font-weight:400}
.footer{position:absolute;left:0;top:982px;width:685px;height:170px;background:var(--purple);border-top:3px solid var(--purple-dark)}
.footer h3{position:absolute;top:18px;font-family:"Lobster",cursive;font-weight:400;color:var(--white);font-size:16px}
.map{position:absolute;left:16px;top:50px;width:205px;height:99px;border:2px solid #3b2163;background:linear-gradient(135deg,#ececec,#dcdcdc 60%,#f3e6a4)}
.footer .field{width:126px;height:26px}
.footer .submit{position:absolute;left:240px;top:122px;width:70px;height:26px;font-size:8px}
.or{position:absolute;left:324px;top:128px;color:#d6c9e8;font-size:10px}
.callus{position:absolute;left:351px;top:120px;color:var(--white);font-size:10px;line-height:12px}
.callus b{display:block;font-size:14px;font-weight:400;line-height:17px}
.links{position:absolute;top:52px;list-style:none}
.links li{display:flex;align-items:center;gap:3px;color:var(--white);font-size:7.6px;height:20.6px}
.links li::before{content:"";width:6px;height:6px;border-radius:50%;background:var(--yellow)}
.bottom-bar{position:absolute;left:0;top:1152px;width:685px;height:48px;background:var(--purple-dark);color:var(--white);font-size:8px;display:flex;align-items:center;justify-content:center}
</style>
</head>
<body>
<div class="star-field left" role="img" aria-label="Neon star pattern on black"></div>
<div class="star-field right" role="img" aria-label="Neon star pattern on black"></div>

<div class="page">
  <header class="header">
    <div class="brand"><span class="dot"></span>Pippa's Party Barn</div>
    <div class="contact-btn btn-blue">CONTACT US</div>
    <div class="phone">
      <svg width="18" height="18" viewBox="0 0 20 20"><circle cx="10" cy="10" r="9" fill="none" stroke="#6c459b" stroke-width="1.6"/><path d="M7 5.5l1.5 2-1 1.2c.6 1.3 1.5 2.2 2.8 2.8l1.2-1 2 1.5-.8 1.5c-3.2-.2-6.3-3.3-6.5-6.5z" fill="#6c459b"/></svg>
      555 010 246 800
    </div>
  </header>

  <nav class="nav">
    <a class="home" href="#">HOME</a>
    <a href="#" style="margin-left:34px">ABOUT</a>
    <a href="#" style="margin-left:48px">AREAS COVERED</a>
    <a href="#" style="margin-left:48px">SERVICES</a>
    <a href="#" style="margin-left:48px">TESTIMONIALS</a>
    <a href="#" style="margin-left:48px">CONTACT</a>
    <a href="#" style="margin-left:48px">FUN STUFF</a>
  </nav>

  <section class="slider">
    <div class="art" role="img" aria-label="Photo of a clown in red and yellow costume with balloons"></div>
    <h1>Pippa's Party Barn entertainment<br>who offers Children's Entertainment<br>Services</h1>
    <div class="dots"><i></i><i class="on"></i><i></i><i></i></div>
  </section>

  <aside class="quick-form">
    <h2>Contact Now</h2>
    <div class="field" style="top:40px">Name</div>
    <div class="field" style="top:70px">Email Address</div>
    <div class="field" style="top:100px">Phone</div>
    <div class="field" style="top:131px">Messages</div>
    <div class="submit btn-blue">SUBMIT</div>
  </aside>

  <h2 class="section-title news-title">Latest News</h2>
  <div class="news-item" style="top:405px">
    <div class="thumb" role="img" aria-label="Photo of children on a stage" style="background:linear-gradient(#c9b8a8,#7a5a55)"></div>
    <p>Lorem ipsum dolor sit amet, consectetur adipiscing elit.</p>
  </div>
  <div class="news-item" style="top:464px">
    <div class="thumb" role="img" aria-label="Illustration of a rainbow slide" style="background:linear-gradient(135deg,#8fd3f0,#e24a7a 60%,#f5c542)"></div>
    <p>Nullam hendrerit, libero nec varius ullamcorper, ante ipsum.</p>
  </div>
  <div class="news-item" style="top:521px">
    <div class="thumb" role="img" aria-label="Photo of a child beside an alarm clock" style="background:linear-gradient(135deg,#d8c6a3,#8a6d4a)"></div>
    <p>Donec lacinia congue ante, nec tempus dolor lacinia eget.</p>
  </div>

  <div class="offers" role="img" aria-label="Silhouette of a tree and balloons against a moonlit sky"><span>Weekend Offers</span></div>

  <section class="grid">
    <div class="tile"><div class="photo" role="img" aria-label="Children at a magic show" style="background:linear-gradient(#c0282a,#5a0f12)"></div><div class="label">Magic Shows</div></div>
    <div class="tile"><div class="photo" role="img" aria-label="Performer in a dark circus scene" style="background:linear-gradient(#555,#111)"></div><div class="label">Circus Clowns</div></div>
    <div class="tile"><div class="photo" role="img" aria-label="Child with face paint as a fairy" style="background:linear-gradient(#6a7d6a,#3c4a3c)"></div><div class="label">Face Painting</div></div>
    <div class="tile"><div class="photo" role="img" aria-label="Children in costumes" style="background:linear-gradient(#f1f1f1,#b8865a)"></div><div class="label">Costume Characters</div></div>
    <div class="tile"><div class="photo" role="img" aria-label="Children with balloons under a blue sky" style="background:linear-gradient(#8fc6ef,#d8b38a)"></div><div class="label">Party Host</div></div>
    <div class="tile"><div class="photo" role="img" aria-label="Child in a carnival party outfit" style="background:linear-gradient(#f3a6c8,#c88a6a)"></div><div class="label">Carnival Parties</div></div>
    <div class="tile"><div class="photo" role="img" aria-label="Children with balloon sculptures in a garden" style="background:linear-gradient(#4f8a3a,#a6c27a)"></div><div class="label">Balloon Sculpting</div></div>
    <div class="tile"><div class="photo" role="img" aria-label="Children dancing at a party" style="background:linear-gradient(#c8b8b0,#6a4a45)"></div><div class="label">DJ and MC</div></div>
    <div class="tile"><div class="photo" role="img" aria-label="Children playing on a lawn" style="background:linear-gradient(#a8c98a,#4e8a2e)"></div><div class="label">Princess Parties</div></div>
    <div class="tile"><div class="photo" role="img" aria-label="Couple on a winter street" style="background:linear-gradient(#d5d9e0,#6c6670)"></div><div class="label">Holiday Parties</div></div>
    <div class="tile"><div class="photo" role="img" aria-label="Cartoon of children in a boat" style="background:linear-gradient(#35d0f0,#f0e040)"></div><div class="label">Fun Add Ons</div></div>
    <div class="tile"><div class="photo" role="img" aria-label="Clown with a dove" style="background:linear-gradient(135deg,#111 40%,#c4231f)"></div><div class="label">Contact</div></div>
  </section>

  <div class="divider"></div>

  <section class="welcome">
    <h2 class="section-title">Welcome To Pippa</h2>
    <p>Lorem ipsum dolor sit amet, consectetur adipiscing elit. Cras ut elit dolor. Donec suscipit feugiat tincidunt. Quisque vestibulum ut ex semper rhoncus. Fusce lectus nisl, venenatis et efficitur quis, efficitur eu massa. Suspendisse semper malesuada sem, at sodales orci varius eget. Fusce gravida sem ac malesuada eleifend. Quisque et condimentum nunc. Donec purus turpis, mattis ac arcu vitae, rutrum hendrerit turpis. Pellentesque ultricies tristique nisl, nec cursus nibh aliquam ac. Nam fringilla lacus nec risus tincidunt commodo. Proin non quam erat. Nullam sed magna id mi lacinia imperdiet.</p>
    <p>Sed et fermentum lectus, nec lobortis quam. Maecenas posuere libero erat, sed tempor justo faucibus a. Aliquam fringilla quis odio non mollis. Sed accumsan arcu at sollicitudin tempor. Nulla tincidunt consectetur sollicitudin. Nunc in magna pellentesque ligula consequat hendrerit non id erat. Cras id lectus eget neque cursus suscipit quis a enim. Curabitur sit amet fermentum turpis. In non viverra dolor, eget sodales quam. Praesent dapibus iaculis hendrerit. Aenean a mauris mi. Phasellus finibus nibh iaculis efficitur hendrerit. Sed luctus, nunc in euismod finibus, nisi orci rutrum ligula, quis lacinia orci felis vel orci.</p>
    <div class="cta btn-blue">CONTACT THE ENTERTAINER</div>
  </section>

  <footer class="footer">
    <h3 style="left:16px">Our Location</h3>
    <div class="map" role="img" aria-label="Street map showing the entertainer's location"></div>

    <h3 style="left:240px">Contact Us</h3>
    <div class="field" style="left:240px;top:50px">Name</div>
    <div class="field" style="left:374px;top:50px">Email Address</div>
    <div class="field" style="left:240px;top:84px">Phone</div>
    <div class="field" style="left:374px;top:84px">Messages</div>
    <div class="submit btn-blue">SUBMIT</div>
    <div class="or">OR</div>
    <div class="callus">CALL US<b>555 010 246 800</b></div>

    <h3 style="left:518px">Quick Links</h3>
    <ul class="links" style="left:518px">
      <li>Home</li><li>About</li><li>Areas Covered</li><li>Services</li><li>Testimonials</li>
    </ul>
    <ul class="links" style="left:597px">
      <li>Fun stuff</li><li>Privacy Policy</li><li>Sitemap</li><li>Contact</li>
    </ul>
  </footer>

  <div class="bottom-bar">Copyrights@ 2015 Pippa. All Right Reserved.</div>
</div>
</body>
</html>
```